i need to create a product label for honey jars i will be selling locally in Louisiana. product name will be Marsh Amber. i would like the label to include a notation "not recommended for infants under 1yrs of age".
net weight will be 16oz. also notate it is 100% raw honey. design would include a scripted font for the name but hoping to include aspect of the "bayou" theme like spanish moss or cypress trees but also include something in the design about honey. if there are any requirements that must be listed on there for sale please include them. artwork needs to be masculine but not set on specific colors.

```html
<!DOCTYPE html>
<html lang="en">
<head>
<meta charset="utf-8">
<title>Marsh Amber – Honey Label Set</title>
<link rel="stylesheet" href="https://fonts.googleapis.com/css2?family=Barlow:wght@400;500;600&family=Barlow+Condensed:wght@700&family=Poppins:wght@400;600;700&display=swap">
<style>
  :root {
    --backdrop: #ababab;
    --label-black: #000000;
    --gold: #d9b44a;
    --gold-light: #f3e3a0;
    --gold-deep: #a9801e;
    --olive: #5b5a2a;
    --white: #ffffff;
    --linen: #e8e5de;
    --ink: #1b1b1b;
    --badge-grey: #9ea3ab;
    --badge-amber: #f2b51f;
  }
  * { box-sizing: border-box; margin: 0; padding: 0; }
  html, body { width: 1065px; height: 1200px; overflow: hidden; }
  body {
    background: var(--backdrop);
    position: relative;
    font-family: "Barlow", sans-serif;
    color: var(--white);
  }

  /* ---------- Lid label ---------- */
  .lid-label {
    position: absolute;
    left: 312px; top: 110px;
    width: 440px; height: 440px;
  }

  /* ---------- Front label ---------- */
  .front-label {
    position: absolute;
    left: 112px; top: 640px;
    width: 400px; height: 473px;
    background: var(--label-black);
    overflow: hidden;
  }
  .front-label__scene {
    position: absolute; inset: 0 0 auto 0;
    height: 300px;
    background: linear-gradient(180deg, #8d8a63 0%, #6a6440 30%, #3d3a22 55%, #141208 80%, var(--label-black) 100%);
  }
  .front-label__origin {
    position: absolute; left: 172px; top: 130px;
    font-size: 12.5px; font-weight: 500; letter-spacing: .2px;
  }
  .brand-name {
    font-family: "Barlow", sans-serif;
    font-weight: 600;
    color: var(--gold);
    line-height: .95;
  }
  .front-label .brand-name {
    position: absolute; left: 0; right: 0; top: 152px;
    text-align: center; font-size: 56px;
  }
  .front-label__claim {
    position: absolute; left: 0; right: 0; top: 283px;
    text-align: center; font-size: 22px; font-weight: 600; letter-spacing: .4px;
  }
  .front-label__banner {
    position: absolute; left: 88px; top: 313px;
    width: 236px; height: 48px;
  }
  .front-label__banner span {
    position: absolute; inset: 0;
    display: flex; align-items: center; justify-content: center;
    font-family: "Barlow Condensed", sans-serif; font-weight: 700;
    font-size: 42px; color: var(--ink); letter-spacing: 1px;
  }
  .front-label__weight {
    position: absolute; left: 0; right: 0; top: 364px;
    text-align: center; font-size: 14px;
  }
  .comb-band {
    position: absolute; left: 0; right: 0; bottom: 0; height: 78px;
    background: linear-gradient(90deg, var(--gold-light) 0%, #e4b64a 25%, var(--gold-deep) 38%, var(--olive) 48%, #c9ad48 60%, #f1e4a2 78%, #fbf4d6 88%, #e9d89a 100%);
  }

  /* ---------- Back label ---------- */
  .back-label {
    position: absolute;
    left: 552px; top: 640px;
    width: 400px; height: 473px;
    background: var(--label-black);
  }
  .back-label .brand-name {
    position: absolute; left: 40px; top: 42px;
    font-size: 30px;
  }
  .back-label__claim {
    position: absolute; left: 196px; top: 56px;
    font-size: 17px; font-weight: 500; letter-spacing: 1px; line-height: 1.2;
    text-align: center;
  }
  .back-label__care {
    position: absolute; left: 32px; top: 110px;
    font-size: 10.3px;
  }
  .infant-notice {
    position: absolute; left: 31px; top: 131px;
    width: 212px; height: 37px;
    background: var(--white); color: var(--ink);
    font-size: 11px; font-weight: 500; text-align: center; line-height: 1.2;
    padding-top: 5px; letter-spacing: .3px;
  }
  .nutrition {
    position: absolute; left: 32px; top: 174px;
    width: 210px;
    border: 2px solid var(--white);
    border-collapse: collapse;
    font-family: "Poppins", sans-serif;
  }
  .nutrition th {
    height: 42px; font-size: 18px; font-weight: 700; text-align: center;
    border-bottom: 2px solid var(--white);
  }
  .nutrition td {
    height: 21px; font-size: 9.5px; font-weight: 600; padding-left: 13px;
    border-top: 1.5px solid var(--white); letter-spacing: .3px;
  }
  .nutrition td.sub { padding-left: 21px; }
  .badge {
    position: absolute; border-radius: 50%;
  }
  .badge--origin {
    left: 272px; top: 140px; width: 70px; height: 70px;
    background: radial-gradient(circle, #ffffff 52%, var(--badge-grey) 54%, var(--badge-grey) 100%);
  }
  .badge--quality {
    left: 274px; top: 218px; width: 66px; height: 66px;
    background: radial-gradient(circle, var(--badge-amber) 60%, #fff4cf 62%, #fff4cf 66%, var(--badge-amber) 68%);
  }
  .contact {
    position: absolute; left: 249px; top: 303px;
    font-size: 10.5px; line-height: 1.3;
  }
  .contact dt { font-weight: 600; }
  .contact dd + dt { margin-top: 6px; }
  .warning {
    position: absolute; left: 31px; top: 408px; width: 340px;
    font-family: "Poppins", sans-serif; font-size: 10px; line-height: 1.25; letter-spacing: .3px;
  }
  .warning strong { display: block; font-weight: 700; }
</style>
</head>
<body>

  <svg class="lid-label" viewBox="0 0 440 440" aria-label="Round lid label">
    <defs>
      <clipPath id="lid-clip"><circle cx="220" cy="220" r="220"/></clipPath>
      <linearGradient id="comb-gold" x1="0" y1="0" x2="1" y2="0">
        <stop offset="0" stop-color="#f3e3a0"/>
        <stop offset=".45" stop-color="#a9801e"/>
        <stop offset=".7" stop-color="#e6c45a"/>
        <stop offset="1" stop-color="#f1c24a"/>
      </linearGradient>
      <path id="lid-top-arc" d="M 32 220 A 188 188 0 0 1 408 220"/>
      <path id="lid-bottom-arc" d="M 48 220 A 172 172 0 0 0 392 220"/>
    </defs>
    <circle cx="220" cy="220" r="220" fill="var(--label-black)"/>
    <g clip-path="url(#lid-clip)">
      <rect x="262" y="22" width="156" height="146" rx="10" fill="url(#comb-gold)" role="img" aria-label="Gold honeycomb cluster"/>
    </g>
    <text font-family="Barlow, sans-serif" font-size="19" font-weight="500" fill="#ffffff" letter-spacing=".5">
      <textPath href="#lid-top-arc" startOffset="11%">Product of Cedar Hollow, La</textPath>
    </text>
    <text font-family="Barlow, sans-serif" font-size="58" font-weight="600" fill="#d9b44a" text-anchor="middle">
      <tspan x="205" y="210">Marsh</tspan>
      <tspan x="250" y="264">Amber</tspan>
    </text>
    <text font-family="Barlow, sans-serif" font-size="20" font-weight="600" fill="#ffffff" letter-spacing="3" text-anchor="middle">
      <textPath href="#lid-bottom-arc" startOffset="50%">100% RAW UNFILTERED HONEY</textPath>
    </text>
  </svg>

  <section class="front-label" aria-label="Front label">
    <div class="front-label__scene" role="img" aria-label="Live oak trees draped in Spanish moss"></div>
    <p class="front-label__origin">Product of Cedar Hollow, La</p>
    <h1 class="brand-name">Marsh<br>Amber</h1>
    <p class="front-label__claim">100% RAW UNFILTERED</p>
    <div class="front-label__banner">
      <svg width="236" height="48" viewBox="0 0 236 48">
        <polygon points="0,0 236,0 218,24 236,48 0,48 18,24" fill="var(--linen)"/>
      </svg>
      <span>HONEY</span>
    </div>
    <p class="front-label__weight">Net Weight: 16 oz (454 g)</p>
    <div class="comb-band" role="img" aria-label="Gold honeycomb pattern"></div>
  </section>

  <section class="back-label" aria-label="Back label">
    <h2 class="brand-name">Marsh<br>Amber</h2>
    <p class="back-label__claim">100% RAW<br>UNFILTERED HONEY</p>
    <p class="back-label__care">Natural honey will crystallize, to liquify, reheat in a pan of warm water</p>
    <p class="infant-notice">NOT RECOMMENDED FOR<br>INFANTS UNDER 1 YEAR OF AGE.</p>
    <table class="nutrition">
      <thead><tr><th>Nutritional Facts</th></tr></thead>
      <tbody>
        <tr><td>Serving Size: 1 tbsp (21g)</td></tr>
        <tr><td>Servings Per Container: About 21</td></tr>
        <tr><td>Calories: 60</td></tr>
        <tr><td>Total Fat: 0g</td></tr>
        <tr><td>Sodium: 0mg</td></tr>
        <tr><td>Total Carbohydrate: 17g</td></tr>
        <tr><td class="sub">Sugars: 17g</td></tr>
        <tr><td>Protein: 0g</td></tr>
      </tbody>
    </table>
    <div class="badge badge--origin" role="img" aria-label="Origin seal"></div>
    <div class="badge badge--quality" role="img" aria-label="Quality seal"></div>
    <dl class="contact">
      <dt>Contact info:</dt>
      <dd>218 Willow Bend Lafourche,<br>La 70394.</dd>
      <dt>Email:</dt>
      <dd>marshamberch@mailbox.com</dd>
    </dl>
    <p class="warning"><strong>WARNING!</strong>product may contain bacteria that can cause illness in infants or those with weakened immune systems.</p>
  </section>

</body>
</html>
```